Looking for a cool & simple business-card-design for digital agency

Hi!

We are a web agency that offers Reputation Management, Vextor & Seo Services and software development. We like cool things, we like innovative styles.

We have uploaded our logo.

Project Deadline Extended Reason: Client does not want any designs with the colorful logo. Please send us submissions ONLY with the blac and white logo. What the client would like to see:1) Back of the card: is a silver logo on a black background2) front of the card with all the data, please use white background and black logo thank you Added Friday, May 8, 2015

Industry/Entity Type

Software

```html
<!DOCTYPE html>
<html lang="en">
<head>
<meta charset="utf-8">
<title>NetStufe AG – Business Card</title>
<link rel="stylesheet" href="https://fonts.googleapis.com/css2?family=Lato:wght@400;700;900&display=swap">
<style>
  :root {
    --page-bg: #d8d5d1;
    --card-bg: #f3f3f1;
    --card-edge: #c9c8c4;
    --ink: #2b2b2b;
    --ink-soft: #3a3a3a;
  }
  * { margin: 0; padding: 0; box-sizing: border-box; }
  html, body {
    width: 1200px;
    height: 969px;
    overflow: hidden;
    background: var(--page-bg);
    font-family: "Lato", sans-serif;
    color: var(--ink);
  }
  .canvas {
    position: relative;
    width: 1200px;
    height: 969px;
  }
  .business-card {
    position: absolute;
    left: 100px;
    top: 208px;
    width: 1000px;
    height: 553px;
    background: var(--card-bg);
    border: 1px solid var(--card-edge);
    border-radius: 4px;
    box-shadow: 0 14px 40px rgba(0,0,0,0.18);
  }
  .brand {
    position: absolute;
    left: 0;
    right: 0;
    top: 92px;
    display: flex;
    justify-content: center;
    align-items: center;
    gap: 22px;
  }
  .brand-square {
    width: 58px;
    height: 58px;
    background: var(--ink);
  }
  .brand-name {
    font-weight: 900;
    font-size: 66px;
    letter-spacing: 1px;
    color: var(--ink);
    line-height: 1;
  }
  .person {
    position: absolute;
    left: 47px;
    top: 266px;
  }
  .person-name {
    font-weight: 700;
    font-size: 33px;
    color: var(--ink);
  }
  .person-role {
    font-weight: 400;
    font-size: 26px;
    color: var(--ink-soft);
    margin-top: 2px;
  }
  .contact-list {
    position: absolute;
    top: 262px;
    list-style: none;
  }
  .contact-list.phones { left: 308px; }
  .contact-list.online { left: 600px; }
  .contact-item {
    display: flex;
    align-items: center;
    gap: 14px;
    height: 56px;
    font-size: 28px;
    color: var(--ink);
  }
  .contact-icon {
    width: 26px;
    height: 26px;
    flex: none;
    fill: var(--ink);
  }
  .services {
    position: absolute;
    left: 0;
    right: 0;
    top: 413px;
    text-align: center;
    font-size: 29px;
    line-height: 38px;
    color: var(--ink-soft);
  }
</style>
</head>
<body>
<main class="canvas">
  <section class="business-card">
    <header class="brand">
      <span class="brand-square"></span>
      <span class="brand-name">NetStufe AG</span>
    </header>

    <div class="person">
      <p class="person-name">Lena Marwick</p>
      <p class="person-role">Director</p>
    </div>

    <ul class="contact-list phones">
      <li class="contact-item">
        <svg class="contact-icon" viewBox="0 0 24 24" aria-hidden="true">
          <path d="M3 8c0-2 4-4 9-4s9 2 9 4v2h-5V8.5c-1-.6-2.5-.9-4-.9s-3 .3-4 .9V10H3z"/>
          <path d="M6 11h12l2 8H4z"/>
        </svg>
        <span>010 555 0142</span>
      </li>
      <li class="contact-item">
        <svg class="contact-icon" viewBox="0 0 24 24" aria-hidden="true">
          <path d="M7 2h10a2 2 0 0 1 2 2v16a2 2 0 0 1-2 2H7a2 2 0 0 1-2-2V4a2 2 0 0 1 2-2zm0 3v13h10V5z"/>
        </svg>
        <span>555 0177 204</span>
      </li>
    </ul>

    <ul class="contact-list online">
      <li class="contact-item">
        <svg class="contact-icon" viewBox="0 0 24 24" aria-hidden="true">
          <path d="M2 5h20v14H2zm2 2v.4l8 5.3 8-5.3V7zm0 2.8V17h16V9.8l-8 5.3z"/>
        </svg>
        <span>info@netstufeag.com</span>
      </li>
      <li class="contact-item">
        <svg class="contact-icon" viewBox="0 0 24 24" aria-hidden="true">
          <circle cx="12" cy="12" r="9.5" fill="none" stroke="#2b2b2b" stroke-width="2"/>
          <ellipse cx="12" cy="12" rx="4" ry="9.5" fill="none" stroke="#2b2b2b" stroke-width="1.8"/>
          <path d="M2.5 12h19M4 7h16M4 17h16" stroke="#2b2b2b" stroke-width="1.6" fill="none"/>
        </svg>
        <span>www.netstufeag.com</span>
      </li>
    </ul>

    <p class="services">Reputation Management, Vextor &amp; Seo Services<br>and Software development.</p>
  </section>
</main>
</body>
</html>
```